Off Campus Housing website service for universities needs corporate brochure

We need a corporate brochure targeted at universities to get them to partner with us to offer an Off-Campus Housing website with housing listings and educational resources for their students. We provide hosted software and support, off-campus housing listings, and educational resources to embed in the university website (i.e http://rentalhub.wvx.edu); the university promotes the service to off-campus students, parents, and faculty/staff. We have a dedicated account executive to work with each university to promote the website to property managers in the schools area who pay to list their properties on the site. We currently partner with over 100 colleges and universities across the country to serve the needs of their off-campus students. Our corporate website is: www.lodgebridgeallies.com.
Updates

Target Market(s)

Universities and Colleges

Industry/Entity Type

Marketing

Font styles to use
Serif

Requirements
Must have
• Our logo
• Our website (www.lodgebridgeallies.com)
• Contact information (this is different than what we used on our previous brochure, image attached):
• Email: sales@lodgebridgeallies.com
• Student image(s) - must be diverse
• Phone: 877-461-7308
Nice to have
• University/Campus image (generic)

```html
<!DOCTYPE html>
<html lang="en">
<head>
<meta charset="utf-8">
<title>Lodge Bridge Allies – Brochure</title>
<link href="https://fonts.googleapis.com/css2?family=Open+Sans:wght@400;600;700;800&display=swap" rel="stylesheet">
<style>
  :root{
    --lavender:#dcdcf0;
    --navy:#14148a;
    --navy-deep:#0c0c66;
    --royal:#0b4fa3;
    --ink:#1a1f6b;
    --card:#ececec;
    --sky:#c3cdf5;
    --white:#ffffff;
  }
  *{margin:0;padding:0;box-sizing:border-box}
  html,body{width:1200px;height:848px;overflow:hidden;background:var(--lavender)}
  .brochure{position:relative;width:1200px;height:848px;overflow:hidden;font-family:"Open Sans",Arial,sans-serif}
  .backdrop{position:absolute;inset:0;width:1200px;height:848px}

  .brand{position:absolute;left:626px;top:46px;width:468px;height:148px;background:var(--white);border:3px solid var(--royal);display:flex;flex-direction:column;justify-content:center;align-items:center;gap:4px}
  .brand-name{font-weight:700;color:var(--royal);font-size:40px;letter-spacing:8px;line-height:1.1;text-align:center}

  .quote{position:absolute;background:var(--card);box-shadow:2px 3px 6px rgba(0,0,0,.25);color:var(--ink)}
  .quote::before{content:"";position:absolute;inset:-6px -4px 6px 4px;background:var(--white);z-index:-1;transform:rotate(-2deg);box-shadow:1px 2px 4px rgba(0,0,0,.15)}
  .quote-main{left:24px;top:34px;width:550px;height:252px;padding:20px 18px 14px 20px;transform:rotate(-3deg)}
  .quote-main .quote-text{font-size:15.2px;line-height:1.6}
  .quote-student{left:132px;top:312px;width:360px;height:124px;padding:10px 10px 10px 0}
  .quote-student .quote-text{font-size:17px;line-height:1.4;padding-left:2px}
  .quote-credit{font-weight:600;font-size:14.5px;line-height:1.35;margin-top:4px}
  .quote-main .quote-credit{padding-left:118px;transform:rotate(3deg);transform-origin:left}
  .quote-student .quote-credit{text-align:right;font-size:17px;margin-top:6px}

  .contact{position:absolute;right:605px;top:712px;text-align:right;color:var(--white)}
  .contact-call{font-weight:800;font-size:19px;color:var(--sky);letter-spacing:.2px}
  .contact-phone{display:flex;align-items:center;justify-content:flex-end;gap:12px;font-weight:700;font-size:39px;margin-top:4px;letter-spacing:.5px}
  .contact-email{display:flex;align-items:center;justify-content:flex-end;gap:14px;font-size:21px;font-weight:600;margin-top:10px;letter-spacing:1px}

  .pitch{position:absolute;left:632px;top:688px;width:560px;color:var(--white)}
  .pitch-head{font-weight:800;font-size:24px;letter-spacing:.2px}
  .pitch-sub{text-align:right;font-weight:800;font-size:20.5px;line-height:1.35;color:#eef0ff;margin-top:2px;text-shadow:1px 1px 0 var(--navy-deep)}
  .pitch-url{font-weight:800;font-size:24px;margin-top:6px;padding-left:110px;letter-spacing:.3px}
</style>
</head>
<body>
<main class="brochure">
  <svg class="backdrop" viewBox="0 0 1200 848">
    <defs>
      <linearGradient id="photoTone" x1="0" y1="0" x2="1" y2="1">
        <stop offset="0" stop-color="#ffffff"/>
        <stop offset=".5" stop-color="#f0f0f0"/>
        <stop offset=".8" stop-color="#cfcfcf"/>
        <stop offset="1" stop-color="#9a9a9a"/>
      </linearGradient>
      <linearGradient id="shadowTone" x1="0" y1="0" x2="1" y2="1">
        <stop offset="0" stop-color="#4a4a4a"/>
        <stop offset="1" stop-color="#1e1e1e"/>
      </linearGradient>
      <linearGradient id="bandTone" x1="0" y1="0" x2="1" y2="0">
        <stop offset="0" stop-color="#0c0c70"/>
        <stop offset=".6" stop-color="#1b1ba6"/>
        <stop offset="1" stop-color="#10108a"/>
      </linearGradient>
    </defs>
    <rect x="0" y="0" width="1200" height="848" fill="url(#photoTone)" role="img" aria-label="Black and white photo looking up into a glass-roofed campus atrium"/>
    <path d="M0,640 L600,640 C450,660 300,700 200,848 L0,848 Z" fill="url(#shadowTone)" role="img" aria-label="Shadowed corner of the atrium photo"/>
    <path d="M0,0 L930,0 C850,60 760,170 660,320 C570,455 430,560 0,600 Z" fill="var(--navy)"/>
    <path d="M0,0 L880,0 C810,60 720,170 620,310 C530,430 400,540 0,575 Z" fill="var(--lavender)"/>
    <path d="M930,0 L1200,0 L1200,14 C1110,6 1000,8 930,0 Z" fill="var(--navy)"/>
    <path d="M0,575 C300,560 480,560 560,585 L1200,600 L1200,610 C900,602 700,600 560,610 C380,612 200,630 0,640 Z" fill="var(--navy)"/>
    <path d="M1200,628 C900,634 600,640 420,654 C290,668 200,730 150,848 L1200,848 Z" fill="#d8d8d8"/>
    <path d="M1200,640 C900,646 610,652 430,666 C300,680 215,742 168,848 L1200,848 Z" fill="url(#bandTone)"/>
  </svg>

  <div class="brand">
    <span class="brand-name">LODGE BRIDGE</span>
    <span class="brand-name">ALLIES</span>
  </div>

  <figure class="quote quote-main">
    <blockquote class="quote-text">"They have gotten to really ‘know us’; they know what we are trying to convey and the relationships that we want to build with our local community. They joined our local apartment association. They attend meetings and parties, getting to know property owners. I’ve dealt with many agencies over the past 25 years in higher education work. They have our best interest at heart. Any idea we have or any possible concern is discussed honestly and openly.”</blockquote>
    <figcaption class="quote-credit">-Dana Whitfield, Director, Student Housing Link, Ridgeview State University</figcaption>
  </figure>

  <figure class="quote quote-student">
    <blockquote class="quote-text">“Very helpful website all around! it<br>definitely helped ease the process of<br>looking for an apartment.”</blockquote>
    <figcaption class="quote-credit">-Talia, Northbrook Student</figcaption>
  </figure>

  <section class="contact">
    <p class="contact-call">JOIN YOUR COLLEAGUES!</p>
    <p class="contact-phone">
      <svg width="34" height="34" viewBox="0 0 24 24" aria-hidden="true"><path fill="#fff" d="M6.6 10.8a15.1 15.1 0 0 0 6.6 6.6l2.2-2.2c.3-.3.7-.4 1-.2 1.1.4 2.300.6 3.6.6.6 0 1 .4 1 1V20c0 .6-.4 1-1 1A17 17 0 0 1 3 4c0-.6.4-1 1-1h3.5c.6 0 1 .4 1 1 0 1.3.2 2.5.6 3.6.1.3 0 .7-.2 1z"/></svg>
      877.461.7308
    </p>
    <p class="contact-email">
      <svg width="36" height="26" viewBox="0 0 36 26" aria-hidden="true"><rect x="1" y="1" width="34" height="24" rx="3" fill="#fff"/><path d="M3 4 L18 15 L33 4" fill="none" stroke="#14148a" stroke-width="2.5"/></svg>
      sales@lodgebridgeallies.com
    </p>
  </section>

  <section class="pitch">
    <h2 class="pitch-head">MORE THAN JUST A WEBSITE,</h2>
    <p class="pitch-sub">A Custom Designed Off Campus<br>Housing Program for Your<br>Unique University!</p>
    <p class="pitch-url">www.lodgebridgeallies.com</p>
  </section>
</main>
</body>
</html>
```